The quiet harbor with an elephant incorporated in the background

Target Market(s)

Real estate

Industry/Entity Type

Real Estate

Contact Information for Business Card

On back on want my name & number
In front I want the business name, "the quiet harbor", below to say staging & design

Logo Text

The quiet harbor

Font styles to use
Serif

Colors
000000

Requirements
Must have
• I want an elephant behind the writing in gold transperant

```html
<!DOCTYPE html>
<html lang="en">
<head>
<meta charset="utf-8">
<title>The Quiet Harbor – Business Card</title>
<link rel="stylesheet" href="https://fonts.googleapis.com/css2?family=Questrial&family=Source+Sans+3:wght@400;600&display=swap">
<style>
  :root {
    --backdrop: #b2b2b2;
    --card-light: #ffffff;
    --card-dark: #231f20;
    --gold: #e0b31a;
    --ink: #1e1e1e;
    --muted: #8a8a8a;
    --rule: #d6d6d6;
  }
  * { margin: 0; padding: 0; box-sizing: border-box; }
  html, body { width: 1200px; height: 900px; overflow: hidden; }
  body {
    position: relative;
    background: var(--backdrop);
    font-family: "Source Sans 3", Arial, sans-serif;
  }
  .card {
    position: absolute;
    top: 306px;
    width: 440px;
    height: 271px;
    border-radius: 10px;
    box-shadow: 0 2px 6px rgba(0,0,0,0.18);
  }
  .card--contact { left: 149px; background: var(--card-light); }
  .card--brand { left: 608px; background: var(--card-dark); }

  .contact-mark {
    position: absolute;
    left: 30px;
    top: 98px;
    width: 150px;
    text-align: center;
  }
  .contact-mark .dot {
    display: block;
    width: 60px; height: 60px;
    margin: 0 auto 10px;
    border-radius: 50%;
    background: var(--gold);
  }
  .contact-mark .name {
    font-family: "Questrial", Arial, sans-serif;
    font-size: 15px;
    color: var(--gold);
    text-transform: uppercase;
    letter-spacing: 0.5px;
  }
  .divider {
    position: absolute;
    left: 188px;
    top: 70px;
    width: 1px;
    height: 144px;
    background: linear-gradient(to bottom, rgba(200,200,200,0), var(--rule) 40%, var(--rule) 60%, rgba(200,200,200,0));
  }
  .details {
    position: absolute;
    left: 235px;
    top: 84px;
    color: var(--ink);
    font-size: 13px;
    line-height: 13px;
  }
  .details .person {
    color: var(--gold);
    font-weight: 600;
    font-size: 17px;
    line-height: 20px;
    margin-bottom: 13px;
  }
  .details .address { margin-bottom: 21px; }
  .details .line { display: flex; align-items: center; gap: 5px; margin-bottom: 5px; }
  .details svg { width: 9px; height: 9px; fill: var(--gold); }

  .brand-lockup {
    position: absolute;
    left: 0; right: 0;
    top: 64px;
    text-align: center;
    font-family: "Questrial", Arial, sans-serif;
  }
  .brand-lockup .dot {
    display: block;
    width: 72px; height: 72px;
    margin: 0 auto 38px;
    border-radius: 50%;
    background: var(--gold);
  }
  .brand-lockup .name {
    color: var(--gold);
    font-size: 27px;
    line-height: 28px;
    text-transform: uppercase;
  }
  .brand-lockup .tagline {
    margin-top: 4px;
    color: var(--muted);
    font-size: 12px;
    letter-spacing: 0.5px;
    text-transform: uppercase;
  }
</style>
</head>
<body>
  <section class="card card--contact">
    <div class="contact-mark">
      <span class="dot"></span>
      <span class="name">The Quiet Harbor</span>
    </div>
    <div class="divider"></div>
    <div class="details">
      <p class="person">Daniel Marsh</p>
      <p class="address">48 Pier Lane, Suite 2<br>Bayview, 204518</p>
      <p class="line">
        <svg viewBox="0 0 10 10" aria-hidden="true"><path d="M2 0.5 L3.6 2.8 L2.8 3.8 Q4 6.2 6.2 7.2 L7.2 6.4 L9.5 8 L8.5 9.5 Q3 9 0.5 1.5 Z"/></svg>
        (044)-555-0182
      </p>
      <p class="line">
        <svg viewBox="0 0 10 10" aria-hidden="true"><path d="M0 2 H10 V8.5 H0 Z M0 2 L5 5.6 L10 2" stroke="#fff" stroke-width="0.8"/></svg>
        hello@quietharbor.com
      </p>
    </div>
  </section>

  <section class="card card--brand">
    <div class="brand-lockup">
      <span class="dot"></span>
      <p class="name">The Quiet Harbor</p>
      <p class="tagline">Staging &amp; Design</p>
    </div>
  </section>
</body>
</html>
```